Web Site Design and Business Card design for Recruiting Company

There are three major tasks in this project:
1) I need to re-design my newly created website www.talvoro.net using the same logo but creating a totally different recruiting template that will apply better for a recruitment site. I want to use the elements of the Talvoro Network logo (which is the road junction) and red, black and gray colors throughout the website. I need someone to both design and launch the site...
2) I would also like to design a double sided business card using the same logo/colors and elements as described above
3) I would also like to have a small thumbnail logo created. As our large logo cannot be previewed easily on the Pelmwork or on Google Chrome tab images

The design should be contemporary, minimalist and slick

```html
<!DOCTYPE html>
<html lang="en">
<head>
<meta charset="utf-8">
<title>Talvoro Network</title>
<link href="https://fonts.googleapis.com/css2?family=Open+Sans:wght@700;800&family=Roboto:wght@400;500;700&display=swap" rel="stylesheet">
<style>
:root{
  --red:#c8001d;
  --red-dark:#7c0010;
  --black:#0a0a0a;
  --gray:#eeeeef;
  --gray-mid:#e2e2e4;
  --text:#222;
  --muted:#666;
  --white:#fff;
}
*{box-sizing:border-box;margin:0;padding:0}
html,body{width:1200px;height:3519px;overflow:hidden}
body{font-family:Roboto,Arial,sans-serif;color:var(--text);background:var(--white);position:relative}
.abs{position:absolute}
.heading{font-family:"Open Sans",Arial,sans-serif;font-weight:800;letter-spacing:-1px;color:var(--black);text-align:center}
.btn-red{background:linear-gradient(180deg,var(--red),var(--red-dark));color:var(--white);font-weight:700;display:flex;align-items:center;justify-content:center;gap:10px;font-size:16px}
.arrow-dot{width:15px;height:15px;border-radius:50%;background:currentColor;display:inline-flex;align-items:center;justify-content:center}
.arrow-dot svg{width:9px;height:9px}
/* top bar */
.topbar{left:0;top:0;width:1200px;height:56px;background:var(--black);color:var(--white)}
.topbar .mail{left:113px;top:17px;font-size:16px;display:flex;gap:10px;align-items:center}
.topbar .phone{left:490px;top:10px;font-size:23px;font-weight:700;display:flex;gap:10px;align-items:center}
.topbar .socials{left:928px;top:16px;display:flex;gap:13px}
.topbar .socials span{width:22px;height:22px;border-radius:50%;background:var(--white);display:block}
/* nav */
.nav{left:0;top:56px;width:1200px;height:88px;background:var(--white)}
.brand{left:108px;top:30px;display:flex;align-items:center;gap:8px;font-family:Roboto,Arial,sans-serif;font-weight:500;font-size:16px;color:var(--black);white-space:nowrap}
.brand .mark{width:14px;height:14px;background:var(--black)}
.nav .links{left:334px;top:34px;display:flex;gap:30px;font-size:16px;font-weight:500;color:var(--black)}
.nav .links .active{color:var(--red)}
.signin{left:948px;top:21px;width:137px;height:47px;border-radius:24px}
/* hero */
.hero{left:0;top:144px;width:1200px;height:498px;background:linear-gradient(100deg,#dfe7e2 0%,#b9c9b4 25%,#d9cfc6 45%,#e8ecef 70%,#c7d8c0 100%)}
.hero-box{left:109px;top:125px;width:979px;height:248px;background:rgba(120,120,125,.55)}
.hero-title{left:0;top:12px;width:979px;font-size:52px;color:var(--white);text-align:center;font-family:"Open Sans",sans-serif;font-weight:800;letter-spacing:-1.5px}
.hero-input{top:100px;width:311px;height:49px;border-radius:25px;background:var(--white);font-size:16px;color:#555;padding:15px 20px}
.hero-btn{left:409px;top:177px;width:164px;height:49px;border-radius:25px}
/* about */
.about-title{left:114px;top:700px;font-size:42px;text-align:left}
.about-text{left:114px;top:758px;width:444px;font-size:15.4px;line-height:28.5px;color:var(--muted);text-align:justify}
.about-btn{left:114px;top:910px;width:172px;height:49px;border-radius:25px}
.about-frame{left:647px;top:682px;width:438px;height:299px;border:3px solid var(--red);background:var(--white);box-shadow:0 4px 12px rgba(0,0,0,.15)}
.about-photo{left:4px;top:6px;width:426px;height:284px;background:linear-gradient(120deg,#6f7478,#c9c9cb 40%,#8c8f93 70%,#d8d8da)}
/* services */
.services{left:0;top:1025px;width:1200px;height:520px;background:var(--gray)}
.svc-title{left:0;top:30px;width:1200px;font-size:41px}
.card{top:168px;width:312px;height:219px;background:var(--white);border-radius:14px;box-shadow:0 2px 10px rgba(0,0,0,.08);text-align:center}
.card .ico{width:108px;height:108px;border-radius:50%;border:1px solid #ccc;margin:16px auto 0;display:flex;align-items:center;justify-content:center}
.card h3{font-size:18px;font-weight:700;margin-top:26px;color:var(--black)}
.card-active{left:443px;top:115px;width:311px;height:325px;border-radius:14px;background:linear-gradient(180deg,var(--red),var(--red-dark));color:var(--white)}
.card-active .ico{width:108px;height:108px;border-radius:50%;background:var(--white);margin:18px auto 0;display:flex;align-items:center;justify-content:center}
.card-active h3{font-size:18px;font-weight:700;text-align:center;margin-top:23px}
.card-active ul{list-style:none;margin:14px 0 0 48px;font-size:14.5px;font-weight:700}
.card-active li{height:31px;display:flex;gap:18px}
.pager{top:237px;width:42px;height:42px;border-radius:50%;background:var(--white);border:1px solid #bbb;display:flex;align-items:center;justify-content:center}
/* jobs */
.jobs-title{left:0;top:1578px;width:1200px;font-size:41px}
.jobs-sub{left:0;top:1640px;width:1200px;text-align:center;font-size:16px;color:var(--black)}
table.jobs{left:112px;top:1691px;width:976px;border-collapse:separate;border-spacing:2px 0}
.jobs th{height:55px;background:linear-gradient(180deg,var(--red),var(--red-dark));color:var(--white);font-size:20px;font-weight:500}
.jobs td{height:70px;background:var(--gray-mid);text-align:center;font-size:16px;font-weight:500;color:var(--black);border-top:4px solid var(--white)}
.load-btn{left:515px;top:2213px;width:196px;height:54px;background:linear-gradient(180deg,#9a0014,var(--red-dark));font-size:16px}
/* blog */
.blog-title{left:0;top:2298px;width:1200px;font-size:41px}
.post{top:2384px;width:318px;height:358px;background:var(--white);box-shadow:0 0 8px rgba(0,0,0,.18);text-align:center}
.post .pic{left:3px;top:3px;width:312px;height:183px}
.post .date{left:3px;top:136px;width:170px;height:42px;background:var(--white);border:1px solid var(--red);color:var(--red);font-size:16px;font-weight:500;display:flex;align-items:center;justify-content:center;gap:10px}
.post h4{position:absolute;top:200px;width:100%;font-size:20px;font-weight:500;color:var(--black)}
.post p{position:absolute;top:240px;left:22px;width:274px;font-size:15px;line-height:26px;color:var(--muted)}
.post .more{left:73px;top:332px;width:172px;height:48px;border-radius:24px;border:1px solid var(--red);background:var(--white);color:var(--red);font-weight:500;font-size:16px;display:flex;align-items:center;justify-content:center;gap:10px}
.post .more.filled{background:linear-gradient(180deg,var(--red),var(--red-dark));color:var(--white);border:none;font-weight:700}
/* testimonials */
.testi{left:0;top:2805px;width:1200px;height:346px;background:linear-gradient(90deg,#e3e3e4,#efefef 50%,#d6d6d8)}
.testi-title{left:0;top:30px;width:1200px;font-size:41px}
.avatar{border-radius:50%;border:3px solid var(--white);box-shadow:0 0 6px rgba(0,0,0,.2)}
.dots{left:410px;top:123px;display:flex;flex-direction:column;gap:9px}
.dots span{width:14px;height:14px;border-radius:50%;background:var(--red)}
.dots span.ring{background:transparent;border:2px solid var(--red)}
.quote{left:518px;top:129px;width:552px;font-size:15px;line-height:23px;color:var(--muted)}
.author{left:518px;top:236px;font-size:16px;color:var(--muted)}
.author b{color:var(--black);font-weight:700}
/* footer */
.footer{left:0;top:3151px;width:1200px;height:312px;background:var(--black);color:var(--white)}
.f-head{font-size:18px;font-weight:700;text-decoration:underline;text-underline-offset:4px}
.f-list{list-style:none;font-size:16px;margin-top:16px}
.f-list li{height:37px;display:flex;gap:14px;align-items:center}
.sub-form{left:767px;top:130px;width:310px;height:42px;background:var(--white);border:2px solid var(--red);display:flex}
.sub-form .field{flex:1;color:#888;font-size:15px;padding:11px 14px;display:flex;gap:10px}
.sub-form .go{width:98px;background:var(--red);color:var(--white);font-weight:700;font-size:15px;display:flex;align-items:center;justify-content:center}
.f-social{left:767px;top:233px;display:flex;gap:12px}
.f-social span{width:36px;height:36px;border-radius:50%;background:var(--white);border:3px solid var(--red)}
.copyright{left:0;top:3463px;width:1200px;height:56px;background:#2a2a2a;color:var(--white);font-size:17px;display:flex;align-items:center;justify-content:center}
</style>
</head>
<body>

<!-- top bar -->
<div class="abs topbar">
  <div class="abs mail"><svg width="16" height="12" viewBox="0 0 16 12" fill="none" stroke="#fff" stroke-width="1.5"><rect x="1" y="1" width="14" height="10"/><path d="M1 1l7 6 7-6"/></svg>info@talvoro.net</div>
  <div class="abs phone"><svg width="20" height="20" viewBox="0 0 24 24" fill="#fff"><path d="M6.6 10.8a15 15 0 006.6 6.6l2.2-2.2c.3-.3.7-.4 1-.2 1.1.4 2.3.6 3.6.6.6 0 1 .4 1 1V20c0 .6-.4 1-1 1A17 17 0 013 4c0-.6.4-1 1-1h3.5c.6 0 1 .4 1 1 0 1.3.2 2.5.6 3.6.1.3 0 .7-.2 1z"/></svg>+1-555-310-2284</div>
  <div class="abs socials"><span></span><span></span><span></span><span></span><span></span></div>
</div>

<!-- nav -->
<div class="abs nav">
  <div class="abs brand"><span class="mark"></span><span>Talvoro Network</span></div>
  <div class="abs links"><span class="active">HOME</span><span>ABOUT US</span><span>SERVICES</span><span>CONTACT US</span><span>REVIEWS</span></div>
  <div class="abs btn-red signin"><svg width="12" height="14" viewBox="0 0 12 14" fill="#fff"><rect x="0" y="6" width="12" height="8" rx="1"/><path d="M3 6V4a3 3 0 016 0v2" fill="none" stroke="#fff" stroke-width="2"/></svg>SIGN IN</div>
</div>

<!-- hero -->
<div class="abs hero" role="img" aria-label="Photo of a smiling woman working on a laptop in a bright room">
  <div class="abs hero-box">
    <div class="abs hero-title">TALVORO NETWORK</div>
    <div class="abs hero-input" style="left:3px">key word</div>
    <div class="abs hero-input" style="left:335px">Select Location</div>
    <div class="abs hero-input" style="left:666px">Experience</div>
    <div class="abs btn-red hero-btn">SEARCH JOBS</div>
  </div>
</div>

<!-- about -->
<h2 class="abs heading about-title">ABOUT US</h2>
<p class="abs about-text">Talvoro Network LLC is an Atlanta based talent advisory, recruiting and staffing firm. We help companies find skilled professionals within the shortest time frames though our unique network of business and personal connections nationwide and overseas.</p>
<div class="abs btn-red about-btn">READ MORE <span class="arrow-dot" style="color:#fff"><svg viewBox="0 0 10 10"><path d="M3 2l4 3-4 3" stroke="#7c0010" stroke-width="2" fill="none"/></svg></span></div>
<div class="abs about-frame"><div class="abs about-photo" role="img" aria-label="Photo of business people shaking hands across a glass meeting table"></div></div>

<!-- services -->
<div class="abs services">
  <h2 class="abs heading svc-title">OUR SERVICES</h2>
  <div class="abs card" style="left:112px">
    <div class="ico"><svg width="64" height="60" viewBox="0 0 64 60" fill="none" stroke="#b00018" stroke-width="2.5"><rect x="6" y="8" width="52" height="34" rx="2"/><path d="M2 46h60v4H2z"/><circle cx="42" cy="18" r="9"/><path d="M14 34l8-8 6 5 8-9"/></svg></div>
    <h3>INFORMATION TECHNOLOGY</h3>
  </div>
  <div class="abs card-active">
    <div class="ico"><svg width="56" height="56" viewBox="0 0 24 24" fill="none" stroke="#b00018" stroke-width="1.4"><path d="M6.6 10.8a15 15 0 006.6 6.6l2.2-2.2c.3-.3.7-.4 1-.2 1.1.4 2.3.6 3.6.6.6 0 1 .4 1 1V20c0 .6-.4 1-1 1A17 17 0 013 4c0-.6.4-1 1-1h3.5c.6 0 1 .4 1 1 0 1.3.2 2.5.6 3.6.1.3 0 .7-.2 1z"/><path d="M14 5a5 5 0 015 5M14 2a8 8 0 018 8"/></svg></div>
    <h3>TELECOMMUNICATIONS</h3>
    <ul><li>»<span>Project Management</span></li><li>»<span>Construction Management</span></li><li>»<span>Site Acquisition</span></li><li>»<span>Cell Site Integration</span></li></ul>
  </div>
  <div class="abs card" style="left:774px">
    <div class="ico"><svg width="60" height="60" viewBox="0 0 60 60" fill="none" stroke="#b00018" stroke-width="2.5"><rect x="10" y="6" width="30" height="44" rx="2"/><rect x="15" y="11" width="20" height="8"/><circle cx="36" cy="40" r="10"/><path d="M36 34v12M33 37h5M33 43h5"/><path d="M46 22l8 8-10 14"/></svg></div>
    <h3>ACCOUNTING &amp; FINANCE</h3>
  </div>
  <div class="abs pager" style="left:28px"><svg width="12" height="18" viewBox="0 0 12 18"><path d="M9 2L2 9l7 7" stroke="#222" stroke-width="2.5" fill="none"/></svg></div>
  <div class="abs pager" style="left:1124px"><svg width="12" height="18" viewBox="0 0 12 18"><path d="M3 2l7 7-7 7" stroke="#222" stroke-width="2.5" fill="none"/></svg></div>
</div>

<!-- job list -->
<h2 class="abs heading jobs-title">JOB LIST</h2>
<p class="abs jobs-sub">Here is a list of jobs grouped by similar occupations</p>
<table class="abs jobs">
  <thead><tr><th style="width:252px">NAME</th><th style="width:222px">LOCATION</th><th style="width:168px">JOB TYPE</th><th style="width:176px">SALARY</th><th>APPLY</th></tr></thead>
  <tbody>
    <tr><td>PROJECT MANAGEMENT</td><td>ANIM ID EST</td><td>TOTAM REM</td><td>$ 15,000</td><td>DIGNISSIMOS</td></tr>
    <tr><td>NETWORK ADMINISTRATION</td><td>PERSPICIATIS UNDE</td><td>NEQUE PORRO</td><td>$ 12,000</td><td>PRAESENTIUM</td></tr>
    <tr><td>SOFTWARE ENGINEERING</td><td>OMNIS ISTE NATUS</td><td>DOLORES EOS</td><td>$ 25,000</td><td>TEMPORE</td></tr>
    <tr><td>MOBILE DEVELOPMENT</td><td>SIT VOLUPTATEM</td><td>SEQUI NESCIUNT</td><td>$ 10,000</td><td>OMNIS DOLOR</td></tr>
    <tr><td>TECHNICAL SUPPORT</td><td>ACCUSANTIUM</td><td>EIUS MODI</td><td>$ 30,000</td><td>REPELLENDUS</td></tr>
    <tr><td>FINANCIAL PLANNING</td><td>DOLOREMQUE LAUDAN</td><td>NOSTRUM</td><td>$ 50,000</td><td>MAIORES</td></tr>
  </tbody>
</table>
<div class="abs btn-red load-btn">LOAD MORE JOBS</div>

<!-- blog -->
<h2 class="abs heading blog-title">LATEST BLOG</h2>
<div class="abs post" style="left:110px">
  <div class="abs pic" role="img" aria-label="Photo of a team meeting in an office" style="background:linear-gradient(120deg,#3a3f4a,#9a8e86 50%,#55606e)"></div>
  <div class="abs date"><svg width="16" height="16" viewBox="0 0 16 16" fill="none" stroke="#c8001d" stroke-width="1.6"><rect x="1" y="3" width="14" height="12"/><path d="M1 7h14M5 1v4M11 1v4"/></svg>20 Sep 2019</div>
  <h4>QUIS AUTEM VEL EUM</h4>
  <p>Sed ut perspiciatis unde omnis iste natus error sit voluptatem accusantium doloremque laudantium.</p>
  <div class="abs more">READ MORE <span class="arrow-dot"><svg viewBox="0 0 10 10"><path d="M3 2l4 3-4 3" stroke="#fff" stroke-width="2" fill="none"/></svg></span></div>
</div>
<div class="abs post" style="left:439px">
  <div class="abs pic" role="img" aria-label="Photo of a job interview between two people" style="background:linear-gradient(120deg,#2e2c2e,#7d8690 55%,#b8bcc0)"></div>
  <div class="abs date"><svg width="16" height="16" viewBox="0 0 16 16" fill="none" stroke="#c8001d" stroke-width="1.6"><rect x="1" y="3" width="14" height="12"/><path d="M1 7h14M5 1v4M11 1v4"/></svg>20 Sep 2019</div>
  <h4>QUIS AUTEM VEL EUM</h4>
  <p>Sed ut perspiciatis unde omnis iste natus error sit voluptatem accusantium doloremque laudantium.</p>
  <div class="abs more filled">READ MORE <span class="arrow-dot" style="color:#fff"><svg viewBox="0 0 10 10"><path d="M3 2l4 3-4 3" stroke="#7c0010" stroke-width="2" fill="none"/></svg></span></div>
</div>
<div class="abs post" style="left:767px">
  <div class="abs pic" role="img" aria-label="Photo of a woman reviewing documents at a desk" style="background:linear-gradient(120deg,#4a4a4c,#c9c6c2 50%,#6d6a68)"></div>
  <div class="abs date"><svg width="16" height="16" viewBox="0 0 16 16" fill="none" stroke="#c8001d" stroke-width="1.6"><rect x="1" y="3" width="14" height="12"/><path d="M1 7h14M5 1v4M11 1v4"/></svg>20 Sep 2019</div>
  <h4>QUIS AUTEM VEL EUM</h4>
  <p>Sed ut perspiciatis unde omnis iste natus error sit voluptatem accusantium doloremque laudantium.</p>
  <div class="abs more">READ MORE <span class="arrow-dot"><svg viewBox="0 0 10 10"><path d="M3 2l4 3-4 3" stroke="#fff" stroke-width="2" fill="none"/></svg></span></div>
</div>

<!-- testimonials -->
<div class="abs testi">
  <h2 class="abs heading testi-title">TESTIMONIALS</h2>
  <div class="abs avatar" role="img" aria-label="Client portrait" style="left:108px;top:85px;width:80px;height:80px;background:linear-gradient(135deg,#8a7a70,#d8d2cc)"></div>
  <div class="abs avatar" role="img" aria-label="Client portrait" style="left:210px;top:57px;width:64px;height:64px;background:linear-gradient(135deg,#6e7680,#c5c8cc)"></div>
  <div class="abs avatar" role="img" aria-label="Featured client portrait" style="left:199px;top:107px;width:144px;height:144px;background:linear-gradient(135deg,#5c6066,#c9bfb6)"></div>
  <div class="abs avatar" role="img" aria-label="Client portrait" style="left:108px;top:185px;width:80px;height:80px;background:linear-gradient(135deg,#6b6a68,#bdb8b0)"></div>
  <div class="abs avatar" role="img" aria-label="Client portrait" style="left:210px;top:248px;width:64px;height:64px;background:linear-gradient(135deg,#b35a3a,#e6c8b6)"></div>
  <div class="abs dots"><span></span><span></span><span class="ring"></span><span></span><span></span></div>
  <svg class="abs" style="left:460px;top:126px" width="38" height="32" viewBox="0 0 38 32" fill="#999"><path d="M0 32V18C0 8 5 2 15 0l1 4C10 6 8 10 8 14h8v18zM22 32V18c0-10 5-16 15-18l1 4c-6 2-8 6-8 10h8v18z"/></svg>
  <p class="abs quote">Ut enim ad minima veniam, quis nostrum exercitationem ullam corporis suscipit laboriosam, nisi ut aliquid ex ea commodi consequatur? Quis autem vel eum iure reprehenderit qui in ea voluptate velit esse quam nihil molestiae consequatur, vel illum qui dolorem eum fugiat quo voluptas nulla pariatur.</p>
  <p class="abs author"><b>MARCUS DELANE ,</b> Employee</p>
</div>

<!-- footer -->
<div class="abs footer">
  <div class="abs" style="left:115px;top:42px"><div class="f-head">QUICK LINKS</div>
    <ul class="f-list"><li>»<span>Home</span></li><li>»<span>About Us</span></li><li>»<span>Services</span></li><li>»<span>Process</span></li><li>»<span>Contact Us</span></li></ul></div>
  <div class="abs" style="left:283px;top:42px"><div class="f-head">OTHER LINKS</div>
    <ul class="f-list"><li>»<span>FAQ</span></li><li>»<span>Help Service</span></li><li>»<span>Terms Of Use</span></li><li>»<span>Policies</span></li><li>»<span>Blog</span></li></ul></div>
  <div class="abs" style="left:463px;top:42px"><div class="f-head">FIND US ON</div>
    <ul class="f-list" style="font-size:15px">
      <li><svg width="14" height="14" viewBox="0 0 14 14" fill="#fff"><path d="M7 0a5 5 0 015 5c0 4-5 9-5 9S2 9 2 5a5 5 0 015-5z"/><circle cx="7" cy="5" r="2" fill="#0a0a0a"/></svg><span>1.10.33 of &nbsp;Finibus Bono</span></li>
      <li><svg width="14" height="14" viewBox="0 0 24 24" fill="#fff"><path d="M6.6 10.8a15 15 0 006.6 6.6l2.2-2.2c.3-.3.7-.4 1-.2 1.1.4 2.3.6 3.6.6.6 0 1 .4 1 1V20c0 .6-.4 1-1 1A17 17 0 013 4c0-.6.4-1 1-1h3.5c.6 0 1 .4 1 1 0 1.3.2 2.5.6 3.6.1.3 0 .7-.2 1z"/></svg><span>+1-555-310-2284</span></li>
      <li><svg width="14" height="11" viewBox="0 0 16 12" fill="none" stroke="#fff" stroke-width="1.5"><rect x="1" y="1" width="14" height="10"/><path d="M1 1l7 6 7-6"/></svg><span>info@talvoro.net</span></li>
      <li><svg width="14" height="14" viewBox="0 0 14 14" fill="#fff"><rect x="0" y="4" width="14" height="10" rx="1"/><rect x="3" y="0" width="8" height="5" fill="none" stroke="#fff" stroke-width="1.5"/></svg><span>888 888 8888</span></li>
    </ul></div>
  <div class="abs" style="left:767px;top:42px"><div class="f-head">SUBSCRIPTION</div>
    <p style="font-size:15px;margin-top:16px;word-spacing:6px">Lorem ipsum dolor sit amet, consectetur</p></div>
  <div class="abs sub-form"><div class="field"><svg width="16" height="12" viewBox="0 0 16 12" fill="none" stroke="#c8001d" stroke-width="1.5"><rect x="1" y="1" width="14" height="10"/><path d="M1 1l7 6 7-6"/></svg>Email</div><div class="go">SUBSCRIBE</div></div>
  <div class="abs f-head" style="left:767px;top:195px">CONNECTED US ON</div>
  <div class="abs f-social"><span></span><span></span><span></span><span></span><span></span></div>
</div>
<div class="abs copyright">© 2019 Talvoro. All Rights Reserved</div>

</body>
</html>
```